Delivery Docket urgent plus require many other designs for more stationary after this.

We need a new delivery docket design urgently as the one we have needs updating and we have changed our company name. Please do not copy the one I have uploaded as we do not feel this looks professional enough. I uploaded it as a few designers requested to see what we are currently using thank you.
It is quite complex in that we need a range of information to be on the one docket.
We are a Transport Company based in Australia that has a wide variety of items that we deliver such as water, sand and gravels and heavy equipment transport.
We would prefer to keep this design to A5 size as we will get them made into books. We are looking for a modern professional look. Although it is only a delivery docket this is given to all our customers so needs to look impressive.

We need our new logo on the docket (WTR). There will also need to be areas for our address and contact numbers, email etc these will be supplied to the winning designer to make the final adjustments so for now just put something generic in these spaces.
Needs to have an area for customer details, purchase order number, date and docket number (docket number to be in red)
Needs a section where we can list the type of product / and or service that has been provided and the amount / qty usually 3 lines will be enough for this. Need area under this where the customer can sign name and print name to say that the goods / and or services have been received.

Also required somewhere on the docket are the words, Tax Invoice will be issued based on the information provided on this docket. Conditions on back of page

We then need a separate section on the same page which we will use internally that the staff member can tear off and hand into the office. On this section it needs to have area where the driver can list km at start of job and at end with space to calculate km travelled, details of fuel purchased eg amount and litres, vehicle that is being used. also need to log down wheel bearing temps.
prime mover needs spaces as follows
Steer axel FL____________ Steer axel FR _________ 1st drive axel L_______
1st drive axel R_________ 2nd drive axel L_______ 2nd drive axel R________

For the trailers need something similar x 2 as have 2 trailers
1st axel DS_________ 1st axel PS_________ 2nd axel DS__________
2nd axel PS_________ 3rd axel DS_________ 3rd axel PS__________

I have included a few examples of designs we have used in past and ones that we like so you can get an idea of the colours we prefer, I have included some of the designs we are currently receiving for our logo that I like so you can get idea again of colours we prefer. There is much more we need designed also such as time sheets, more delivery dockets and letter heads so there is a lot of more work available to the winning designer.

Thank you

Customers

Serif
Sans Serif

Designer to choose colors to be used in the design.

• Please don't copy old docket as we do not like it and nned new info on new design thank you

```html
<!DOCTYPE html>
<html lang="en">
<head>
<meta charset="utf-8">
<title>WTR Delivery Docket</title>
<link href="https://fonts.googleapis.com/css2?family=Arimo:wght@400;700&display=swap" rel="stylesheet">
<style>
  :root {
    --page-bg: #d9d9d9;
    --paper: #ffffff;
    --ink: #111111;
    --band: #3f3f3f;
    --cell: #e2e2e2;
    --label: #444444;
    --accent-red: #e0141b;
    --tab-light: #e6e6e6;
    --log-bg: #ebebeb;
  }
  html, body {
    margin: 0;
    padding: 0;
    width: 798px;
    height: 1200px;
    overflow: hidden;
    background: var(--page-bg);
    font-family: "Arimo", Arial, sans-serif;
  }
  .docket {
    position: absolute;
    left: 0;
    top: 300px;
    width: 832px;
    height: 640px;
    background: var(--paper);
    transform: scale(0.959);
    transform-origin: 0 0;
    color: var(--ink);
  }
  .docket > * { position: absolute; box-sizing: border-box; }

  .masthead {
    left: 0; top: 0; width: 832px; height: 128px;
    background: linear-gradient(90deg, #1a1a1a 0%, #2e2e2e 40%, #6f6f6f 60%, #9a9a9a 80%, #7a7a7a 100%);
  }
  .masthead-name {
    left: 36px; top: 30px;
    font-size: 64px; font-weight: 700; letter-spacing: 4px;
    color: #cfcfcf;
  }

  .company { left: 46px; top: 148px; font-size: 11px; line-height: 13px; }
  .company-name { font-size: 16px; font-weight: 700; line-height: 18px; }

  .band { background: var(--band); color: #fff; font-weight: 700; }
  .depot { left: 43px; top: 246px; width: 185px; height: 60px; padding: 4px 6px; font-size: 12px; line-height: 15px; }

  .section-head { font-size: 14px; padding: 7px 8px; height: 29px; }
  .customer-head { left: 245px; top: 147px; width: 337px; }
  .docket-head {
    left: 587px; top: 147px; width: 205px; height: 29px;
    background: var(--tab-light); color: var(--ink);
    font-size: 14px; font-weight: 700; padding: 4px 10px;
  }
  .docket-number { color: var(--accent-red); font-size: 20px; margin-left: 6px; vertical-align: -2px; }

  .field { background: var(--cell); font-size: 10.5px; color: var(--label); padding: 5px 6px; }
  .field b { display: block; text-align: right; width: 80px; color: var(--ink); }
  .date-line { margin-left: 40px; font-size: 16px; color: var(--ink); letter-spacing: 1px; }

  .col-head { top: 316px; height: 28px; font-size: 14px; text-align: center; padding-top: 7px; }
  .row-cell { background: var(--cell); height: 29px; }

  .tax-bar {
    left: 42px; top: 477px; width: 750px; height: 15px;
    font-size: 10px; font-weight: 400; text-align: center; line-height: 15px;
  }
  .received-label { left: 42px; top: 495px; width: 128px; height: 20px; font-size: 10.5px; padding: 4px 4px; }
  .received-field { top: 495px; height: 20px; padding: 3px 6px; font-size: 10.5px; }

  .tear-line { left: 0; top: 529px; width: 832px; border-top: 2px dashed #c8c8c8; }

  .driver-log {
    left: 15px; top: 537px; width: 802px; height: 24px;
    display: flex; gap: 4px;
  }
  .driver-cell {
    flex: 1 1 auto; background: var(--log-bg);
    font-size: 9px; line-height: 24px; color: #333;
    padding: 0 6px; white-space: nowrap;
  }
  .driver-cell b { color: var(--ink); }

  .log-box {
    top: 566px; height: 38px; background: var(--log-bg);
    font-size: 9px; line-height: 13px; color: #333; padding: 6px 7px; white-space: pre;
  }
</style>
</head>
<body>
<div class="docket">
  <div class="masthead" role="img" aria-label="Dark metallic banner with a photo of two prime mover trucks on the right"></div>
  <div class="masthead-name">WTR</div>

  <div class="company">
    <div class="company-name">WTR</div>
    412 W HALBERT ROAD MESA<br>
    AZ 85201 USA<br>
    TELEPHONE : 555 0142 318<br>
    FAX: 555 0142 319<br>
    EMAIL: accounts@WTRHAUL.COM
  </div>
  <div class="band depot">DEPOT: STREET ADDRESS<br>TOWN<br>Phone: 000 000 000</div>

  <div class="band section-head customer-head">CUSTOMER DETAILS</div>
  <div class="docket-head">DELIVERY DOCKET<span class="docket-number">2050</span></div>

  <div class="field" style="left:245px;top:180px;width:337px;height:30px;">Business Name:<b>ABN:</b></div>
  <div class="field" style="left:245px;top:212px;width:337px;height:30px;padding-top:9px;">Order Number:</div>
  <div class="field" style="left:245px;top:245px;width:337px;height:30px;padding:9px 0 0 42px;">Contact:</div>
  <div class="field" style="left:245px;top:278px;width:547px;height:28px;padding-top:8px;">Billing Address:</div>
  <div class="field" style="left:587px;top:180px;width:205px;height:30px;">Date: <span class="date-line">/__ /__ /_____</span></div>
  <div class="field" style="left:587px;top:212px;width:205px;height:30px;"></div>
  <div class="field" style="left:587px;top:245px;width:205px;height:30px;">Phone:</div>

  <div class="band col-head" style="left:42px;width:110px;">QTY</div>
  <div class="band col-head" style="left:156px;width:570px;">DESCRIPTION</div>
  <div class="band col-head" style="left:730px;width:62px;">PRICE</div>

  <div class="row-cell" style="left:42px;top:348px;width:110px;"></div>
  <div class="row-cell" style="left:156px;top:348px;width:570px;"></div>
  <div class="row-cell" style="left:730px;top:348px;width:62px;"></div>
  <div class="row-cell" style="left:42px;top:380px;width:110px;"></div>
  <div class="row-cell" style="left:156px;top:380px;width:570px;"></div>
  <div class="row-cell" style="left:730px;top:380px;width:62px;"></div>
  <div class="row-cell" style="left:42px;top:412px;width:110px;"></div>
  <div class="row-cell" style="left:156px;top:412px;width:570px;"></div>
  <div class="row-cell" style="left:730px;top:412px;width:62px;"></div>
  <div class="row-cell" style="left:42px;top:443px;width:110px;"></div>
  <div class="row-cell" style="left:156px;top:443px;width:570px;"></div>
  <div class="row-cell" style="left:730px;top:443px;width:62px;"></div>

  <div class="band tax-bar">Tax Invoice will be issued based on the information provided on this docket. Conditions on back of page</div>

  <div class="band received-label">GOODS RECEIVED BY:</div>
  <div class="field received-field" style="left:174px;width:367px;">PRINTED NAME:</div>
  <div class="field received-field" style="left:545px;width:247px;">SIGNED:</div>

  <div class="tear-line"></div>

  <div class="driver-log">
    <div class="driver-cell"><b>Vehicle:</b> ____________</div>
    <div class="driver-cell"><b>KM Start:</b> ________</div>
    <div class="driver-cell"><b>KM End:</b> ________</div>
    <div class="driver-cell"><b>KM Travelled:</b> ________</div>
    <div class="driver-cell"><b>Fuel $:</b> _______</div>
    <div class="driver-cell"><b>Litres:</b> _______</div>
  </div>

  <div class="log-box" style="left:15px;width:300px;">Steer axel FL______ Steer axel FR ______ 1st drive axel L______
1st drive axel R_____ 2nd drive axel L_____ 2nd drive axel R_____</div>
  <div class="log-box" style="left:319px;width:250px;">1st axel DS_____ 1st axel PS_____ 2nd axel DS_____
2nd axel PS_____ 3rd axel DS_____ 3rd axel PS_____</div>
  <div class="log-box" style="left:573px;width:244px;">1st axel DS_____ 1st axel PS_____ 2nd axel DS_____
2nd axel PS_____ 3rd axel DS_____ 3rd axel PS_____</div>
</div>
</body>
</html>
```